Games for Pupils Website Redesign

The purpose of the website redesign is to freshen up the content and update it to give a more modern look and feel. It will show what we do concisely and satisfy all potential visitors. We work with primary schools and the brand is fun.About: Games for Pupils is a scheme that brings top Olympic athletes into primary schools to inspire children to do more physical activity. We typically run a half day event at the school where the athlete does a fun fitness circuit with the children and then an inspirational assembly with a demonstration and Q&A. The children are asked to collect sponsorship money to take part in the event and a large proportion of the money raised goes back to the school in the form of a voucher for them to spend on new sports equipment. 1. To generate more leads from potential customers/schools2. To engage the children and parents more in the event and get them excited for their upcoming visit whilst setting up a fundraiser page.3. To simplify and modernise what is already there.

I have attached some ideas for each of the pages (uploaded in brief)

Here is a link to our current website: www.gamesforpupils.example

I have also attached a link to the sponsorship form which shows the kind of look and feel we're after.

Target Market(s)

Primary school teachers
Primary school parents

Number of Pages Required

5+ page

Requirements
Must have
• Fun, modern.
• Be built on kestrel framekit

```html
<!DOCTYPE html>
<html lang="en">
<head>
<meta charset="utf-8">
<title>Educate – Games for Pupils</title>
<link rel="stylesheet" href="https://fonts.googleapis.com/css2?family=Montserrat:wght@400;500;600;700;800&display=swap">
<style>
:root{
  --green:#33cc14;
  --green-soft:#bdeeb0;
  --green-haze:rgba(189,238,176,0);
  --orange:#ff6a1a;
  --orange-soft:#ff8a4c;
  --orange-haze:rgba(255,138,76,0);
  --orange-card:#f5793a;
  --ink:#1a1a1a;
  --text:#3a3a3a;
  --white:#ffffff;
  --footer:#1e1e1e;
  --footer-text:#d8d8d8;
}
*{box-sizing:border-box;margin:0;padding:0}
html,body{width:769px;height:1200px;overflow:hidden;background:var(--white)}
body{font-family:"Montserrat",Arial,sans-serif;color:var(--text);position:relative}
.page{position:relative;width:769px;height:1200px;overflow:hidden}
.abs{position:absolute}

.ornament{position:absolute;border-radius:50%;background:radial-gradient(closest-side,var(--green-soft) 0%,var(--green-soft) 45%,var(--green-haze) 100%);opacity:.75}
.ornament-small{position:absolute;border-radius:50%;background:radial-gradient(closest-side,var(--green-soft) 0%,var(--green-haze) 100%)}
.quote-ornament{position:absolute;border-radius:12px;background:radial-gradient(closest-side,var(--orange-soft) 0%,var(--orange-soft) 40%,var(--orange-haze) 100%)}

.site-header{position:absolute;top:0;left:0;width:769px;height:60px;background:var(--white);border-bottom:1px solid #f0f0f0;z-index:3}
.brand{position:absolute;left:42px;top:24px;display:flex;align-items:center;gap:5px;font-weight:700;font-size:9px;color:var(--ink)}
.brand-dot{width:12px;height:12px;border-radius:50%;background:var(--green)}
.menu-toggle{position:absolute;right:37px;top:26px;display:flex;align-items:center;gap:9px;font-size:8px;font-weight:700;letter-spacing:.5px;color:var(--ink)}
.menu-bars{display:flex;flex-direction:column;gap:3px}
.menu-bars span{display:block;width:23px;height:2px}

.page-title{position:absolute;top:110px;left:0;width:769px;text-align:center;font-size:20px;font-weight:700;color:var(--ink);letter-spacing:.3px;z-index:2}

.info-block{position:absolute;left:133px;width:250px;z-index:2}
.info-heading{display:flex;align-items:center;gap:2px}
.info-heading span{background:var(--green);color:var(--white);font-weight:700;font-size:10.5px;padding:4px 8px;border-radius:2px;white-space:nowrap}
.info-block p{margin:6px 0 0 16px;font-size:7.2px;line-height:9.2px;color:var(--text)}

.promo{position:absolute;z-index:2}
.promo-frame{position:absolute;border:2px solid var(--ink);border-radius:4px}
.promo-card{position:absolute;border-radius:4px;color:var(--white)}
.promo-title{font-weight:700;text-transform:uppercase}
.btn{position:absolute;background:var(--white);border-radius:2px;font-size:7px;font-weight:600;text-align:center;line-height:23px;height:23px;width:85px;text-transform:uppercase}
.card-photo{position:absolute;left:18px;top:84px;width:152px;height:94px;border-radius:3px;background:linear-gradient(160deg,#46524a 0%,#6d6c66 45%,#4a4440 100%)}

.feedback{position:absolute;left:0;top:725px;width:769px;height:239px;background:var(--orange);color:var(--white);overflow:hidden}
.feedback h2{position:absolute;left:152px;top:27px;font-size:13.6px;font-weight:700;line-height:18px}
.feedback h3{position:absolute;left:152px;top:96px;font-size:9.5px;font-weight:700}
.feedback blockquote{position:absolute;left:152px;top:115px;width:455px;font-size:7.2px;line-height:10px}
.feedback cite{position:absolute;left:152px;top:175px;font-size:7.5px;font-weight:700;font-style:normal}
.dots{position:absolute;left:353px;top:208px;display:flex;gap:7px}
.dots span{width:10px;height:10px;border-radius:50%;background:#f0e6e0}
.dots span.active{background:var(--orange);border:2px solid #f0e6e0}

.site-footer{position:absolute;left:0;top:964px;width:769px;height:236px;background:var(--footer);color:var(--footer-text);text-align:center;font-size:6.3px;letter-spacing:.4px}
.footer-links{position:absolute;top:24px;width:100%}
.footer-brand{position:absolute;top:64px;width:100%;display:flex;justify-content:center;align-items:center;gap:5px;font-size:9px;font-weight:700;color:var(--white);letter-spacing:0}
.footer-brand i{display:block;width:11px;height:11px;border-radius:50%;background:var(--white)}
.footer-legal{position:absolute;top:91px;width:100%;line-height:9px}
.footer-contact{position:absolute;top:124px;width:100%;line-height:9px}
.footer-contact b{color:var(--green);font-weight:500}
.social{position:absolute;top:176px;width:100%;display:flex;justify-content:center;gap:7px}
.social span{width:11px;height:11px;background:var(--green);border-radius:1px}
.copyright{position:absolute;top:207px;width:100%}
</style>
</head>
<body>
<div class="page">

  <div class="ornament" style="left:365px;top:10px;width:90px;height:60px" role="img" aria-label="Decorative pale green shape"></div>
  <div class="ornament" style="left:680px;top:88px;width:110px;height:130px" role="img" aria-label="Decorative pale green shape"></div>
  <div class="ornament" style="left:-20px;top:200px;width:170px;height:95px" role="img" aria-label="Decorative pale green shape"></div>
  <div class="ornament" style="left:620px;top:385px;width:80px;height:145px" role="img" aria-label="Decorative pale green shape"></div>
  <div class="ornament" style="left:0;top:590px;width:145px;height:135px" role="img" aria-label="Decorative pale green shape"></div>
  <div class="ornament" style="left:612px;top:675px;width:70px;height:60px" role="img" aria-label="Decorative pale green shape"></div>
  <div class="ornament-small" style="left:296px;top:72px;width:150px;height:82px" role="img" aria-label="Small decorative green accents around the title"></div>

  <header class="site-header">
    <div class="brand"><span class="brand-dot"></span>Games for Pupils</div>
    <div class="menu-toggle">
      <div class="menu-bars"><span style="background:var(--green)"></span><span style="background:var(--orange)"></span><span style="background:#2b8fe0"></span></div>
      MENU
    </div>
  </header>

  <h1 class="page-title">EDUCATE</h1>

  <section class="info-block" style="top:238px">
    <div class="info-heading"><svg width="12" height="14" viewBox="0 0 12 14"><path d="M1.5 1.5 L10.5 7 L1.5 12.5 Z" fill="none" stroke="var(--ink)" stroke-width="1.6"/></svg><span>WHAT’S INVOLVED ?</span></div>
    <p>Lorem ipsum dolor sit amet, consectetur adipiscing elit, sed do eiusmod tempor incididunt ut labore et dolore magna aliqua. Quis ipsum suspendisse ultrices gravida. Risus commodo viverra maecenas accumsan lacus vel facilisis. Lorem ipsum dolor sit amet, consectetur adipiscing elit, sed do eiusmod tempor incididunt ut labore et dolore magna aliqua. Quis ipsum</p>
  </section>
  <section class="info-block" style="top:341px">
    <div class="info-heading"><svg width="12" height="14" viewBox="0 0 12 14"><path d="M1.5 1.5 L10.5 7 L1.5 12.5 Z" fill="none" stroke="var(--ink)" stroke-width="1.6"/></svg><span>WHY IS IT IMPORTANT ?</span></div>
    <p style="margin-top:9px">Lorem ipsum dolor sit amet, consectetur adipiscing elit, sed do eiusmod tempor incididunt ut labore et dolore magna aliqua. Quis ipsum suspendisse ultrices gravida. Risus commodo viverra maecenas accumsan lacus vel facilisis. Lorem ipsum dolor sit amet, consectetur adipiscing elit, sed do eiusmod tempor incididunt ut labore et dolore magna aliqua. Quis ipsum</p>
  </section>
  <section class="info-block" style="top:442px">
    <div class="info-heading"><svg width="12" height="14" viewBox="0 0 12 14"><path d="M1.5 1.5 L10.5 7 L1.5 12.5 Z" fill="none" stroke="var(--ink)" stroke-width="1.6"/></svg><span>HOW MUCH DOES IT COST ?</span></div>
    <p>Lorem ipsum dolor sit amet, consectetur adipiscing elit, sed do eiusmod tempor incididunt ut labore et dolore magna aliqua. Quis ipsum suspendisse ultrices gravida. Risus commodo viverra maecenas accumsan lacus vel facilisis. Lorem ipsum dolor sit amet, consectetur adipiscing elit, sed do eiusmod tempor incididunt ut labore et dolore magna aliqua. Quis ipsum</p>
  </section>

  <aside class="promo promo-download">
    <div class="promo-frame" style="left:439px;top:235px;width:190px;height:108px"></div>
    <div class="promo-card" style="left:446px;top:229px;width:189px;height:107px;background:var(--orange-card)">
      <div class="promo-title" style="text-align:center;font-size:17.5px;line-height:22px;margin-top:17px">DOWNLOAD<br>TOP TIPS</div>
      <div class="btn" style="left:52px;top:65px;color:var(--orange)">Download</div>
    </div>
  </aside>

  <aside class="promo promo-workshops">
    <div class="promo-frame" style="left:442px;top:402px;width:188px;height:231px"></div>
    <div class="promo-card" style="left:448px;top:395px;width:187px;height:231px;background:var(--green)">
      <div class="promo-title" style="margin:19px 0 0 19px;font-size:14.5px;line-height:18px">FIND OUT MORE<br>ABOUT OUR<br>WORKSHOPS</div>
      <div class="card-photo" role="img" aria-label="Photo of an athlete leading a workshop with pupils in a classroom"></div>
      <div class="btn" style="left:50px;top:191px;color:var(--green)">Read more</div>
    </div>
  </aside>

  <section class="feedback">
    <div class="quote-ornament" style="left:85px;top:10px;width:100px;height:80px" role="img" aria-label="Faint decorative shape behind the heading"></div>
    <div class="quote-ornament" style="left:585px;top:118px;width:100px;height:80px" role="img" aria-label="Faint decorative shape beside the testimonial"></div>
    <h2>We’re really proud of our unprompted and unedited feedback.<br>Here’s what are schools have said about us...</h2>
    <h3>Willowbank Infants’ School (23rd June 2018)</h3>
    <blockquote>I just wanted to say thank you for such a fabulous day on Friday. It was absolutely brilliant from start to finish and it ran so smoothly. Everyone commented on how professional and inspirational the whole day was. The athlete’s assembly was just perfect, we really couldn’t have asked for a better day. When I went out to the playground at lunch time, I saw so many children practising their triple jump and encouraging others to join in – what more could we ask for? I am hoping that we will be able to have you in again at some point next year as the day was such a success. Thank you once again.</blockquote>
    <cite>Jo (PE Coordinator)</cite>
    <div class="dots"><span></span><span></span><span></span><span class="active"></span></div>
  </section>

  <footer class="site-footer">
    <div class="footer-links">SITEMAP | COOKIES | PRIVACY POLICY | ONLINE FUNDRAISING</div>
    <div class="footer-brand"><i></i>Games for Pupils</div>
    <div class="footer-legal">Games for Pupils and GFP Coaching are trading names of the Social Enterprise<br>called Playwell Ventures Limited, a company registered in England no. 00000000.</div>
    <div class="footer-contact">
      <b>Telephone:</b> 01000 000000 (GB) or 01 000 0000 (Ireland)<br>
      <b>Email:</b> hello@gamesforpupils.example<br>
      <b>Snailmail (we love a letter!):</b><br>
      GAMES for PUPILS 2 Meadow Yard, Brookfield Park, Easton EA1 0AA<br>
      GAMES for PUPILS Harbour House, Quay Street, Westport Ireland
    </div>
    <div class="social"><span></span><span></span><span></span></div>
    <div class="copyright">© 2019 GAMES FOR PUPILS</div>
  </footer>

</div>
</body>
</html>
```